Heron Loan Partners Business Card

We need a business card design for our mortgage servicing company. In addition to servicing the loans of homeowners, we help homeowners with purchasing their homes and any mortgage refinancing. We would like to see designs that use the colors in the logo attached below (gold-ish yellow and navy blue), and any other design you deem fit! The design should communicate a simpler life with smart mortgages provided by Heron.

```html
<!DOCTYPE html>
<html lang="en">
<head>
<meta charset="utf-8">
<title>Heron Mortgage Business Card</title>
<link rel="stylesheet" href="https://fonts.googleapis.com/css2?family=Montserrat:wght@500;600;800&display=swap">
<style>
  :root {
    --gold: #e0b23c;
    --navy: #24224f;
    --ink: #1c1c1c;
    --paper: #ffffff;
    --backdrop: #4a4a4a;
  }
  * { box-sizing: border-box; margin: 0; padding: 0; }
  html, body { width: 1200px; height: 900px; overflow: hidden; }
  body {
    background: var(--backdrop);
    font-family: "Montserrat", Arial, sans-serif;
    position: relative;
  }
  .card {
    position: absolute;
    width: 660px;
    height: 377px;
    background: var(--paper);
    overflow: hidden;
    box-shadow: 0 6px 18px rgba(0,0,0,.35);
  }
  .card--front { left: 270px; top: 40px; }
  .card--back  { left: 270px; top: 470px; }

  .wordmark {
    display: flex;
    align-items: center;
    gap: 14px;
    color: var(--navy);
    font-weight: 800;
    letter-spacing: 1px;
  }
  .wordmark__dot {
    border-radius: 50%;
    background: var(--navy);
    flex: none;
  }
  .card--front .wordmark {
    position: absolute;
    left: 50%; top: 50%;
    transform: translate(-50%, -50%);
    font-size: 52px;
  }
  .card--front .wordmark__dot { width: 26px; height: 26px; }

  .card--back .wordmark {
    position: absolute;
    right: 60px; top: 64px;
    font-size: 28px;
    gap: 10px;
  }
  .card--back .wordmark__dot { width: 15px; height: 15px; }

  .holder {
    position: absolute;
    left: 0; top: 62px;
    display: flex;
    align-items: stretch;
  }
  .holder__bar { width: 32px; background: var(--gold); margin-top: 26px; height: 28px; }
  .holder__text { padding-left: 20px; }
  .holder__name {
    font-weight: 800;
    font-size: 19px;
    letter-spacing: .5px;
    color: var(--navy);
  }
  .holder__name span { color: var(--gold); }
  .holder__role { font-weight: 500; font-size: 15px; color: var(--ink); margin-top: 2px; }

  .address {
    position: absolute;
    right: 42px; top: 188px;
    text-align: left;
    font-size: 14px;
    font-weight: 500;
    line-height: 1.35;
    color: var(--ink);
  }

  .contacts {
    position: absolute;
    left: 120px; top: 228px;
    list-style: none;
  }
  .contacts li {
    display: flex;
    align-items: center;
    gap: 10px;
    font-size: 15px;
    font-weight: 500;
    color: var(--ink);
    line-height: 25px;
  }
  .contacts svg { width: 15px; height: 15px; fill: var(--gold); flex: none; }

  .stripes { position: absolute; left: 0; bottom: 0; width: 660px; height: 90px; }
</style>
</head>
<body>

  <section class="card card--front" aria-label="Card front">
    <div class="wordmark"><span class="wordmark__dot"></span>Heron Mortgage</div>
  </section>

  <section class="card card--back" aria-label="Card back">
    <div class="holder">
      <div class="holder__bar"></div>
      <div class="holder__text">
        <p class="holder__name">DARA <span>WELLSLEY</span></p>
        <p class="holder__role">Owner</p>
      </div>
    </div>

    <div class="wordmark"><span class="wordmark__dot"></span>Heron Mortgage</div>

    <p class="address">482 Larkspur Ave, Ste<br>210, Dallas, TX 75204</p>

    <ul class="contacts">
      <li>
        <svg viewBox="0 0 16 16" aria-hidden="true"><path d="M3 1h3l1.5 4-2 1.3a9 9 0 0 0 4.2 4.2L11 8.5l4 1.5v3a2 2 0 0 1-2 2A12 12 0 0 1 1 3a2 2 0 0 1 2-2z"/></svg>
        555.014.2290
      </li>
      <li>
        <svg viewBox="0 0 16 16" aria-hidden="true"><path d="M1 3h14v10H1z M2 4l6 5 6-5" fill="none" stroke="#e0b23c" stroke-width="1.6"/></svg>
        info@heronmortgage.com
      </li>
      <li>
        <svg viewBox="0 0 16 16" aria-hidden="true"><circle cx="8" cy="8" r="7"/><path d="M4 6h3v3H5z M9 9h3v3H9z" fill="#fff"/></svg>
        www.heronmortgage.com
      </li>
    </ul>

    <svg class="stripes" viewBox="0 0 660 90" aria-hidden="true">
      <rect x="0" y="76" width="660" height="14" fill="#e0b23c"/>
      <polygon points="0,56 470,56 486,36 660,36 660,70 0,70" fill="#e0b23c"/>
      <rect x="0" y="42" width="190" height="7" fill="#e0b23c"/>
      <rect x="196" y="42" width="124" height="7" fill="#24224f"/>
      <polygon points="326,42 464,42 476,28 660,28 660,31 479,31 467,49 326,49" fill="#e0b23c"/>
    </svg>
  </section>

</body>
</html>
```